Home Remodeling company needs a business card design

we need a business card design for home remodeling company in hamilton county, indiana USA. we offers a wide range of construction services including whole house renovations, Design and Build Basements and Kitchen and Bathroom Remodeling . we would like to see designs for both site of business card that use the same color of the company logo and also including all information below :
1- Karim Feltous CEO / General Contractor
2- all company contacts Telephone numbers ( 1-888-DULOM-47 ) ( 317-555-0193) email address ( info@dulomhome.com) website ( www.dulomhome.com ) and social media logos (Facebook- twitter- google plus )
3- company logo
4- licensed . insured . bonded

```html
<!DOCTYPE html>
<html lang="en">
<head>
<meta charset="utf-8">
<title>Dulom Home Remodeling – Business Card</title>
<link href="https://fonts.googleapis.com/css2?family=Montserrat:wght@700;800&family=Roboto:wght@400;500&display=swap" rel="stylesheet">
<style>
  :root {
    --bg: #e4e2df;
    --card-dark: #2e2e2e;
    --card-light: #f4f4f4;
    --ink: #333333;
    --ink-soft: #555555;
    --accent: #d42a34;
    --white: #ffffff;
  }
  * { box-sizing: border-box; margin: 0; padding: 0; }
  html, body { width: 1200px; height: 716px; overflow: hidden; }
  body {
    background: var(--bg);
    font-family: "Roboto", Arial, sans-serif;
    position: relative;
  }
  .card {
    position: absolute;
    top: 204px;
    width: 540px;
    height: 309px;
    border-radius: 4px;
    box-shadow: 0 10px 24px rgba(0,0,0,0.18);
    overflow: hidden;
  }
  .card-back { left: 40px; background: var(--card-dark); }
  .card-front { left: 620px; background: var(--card-light); }

  .brand {
    display: flex;
    align-items: flex-start;
    gap: 10px;
    font-family: "Montserrat", Arial, sans-serif;
    font-weight: 800;
  }
  .brand-mark { width: 12px; height: 12px; background: var(--accent); margin-top: 10px; }
  .brand-name { font-size: 46px; line-height: 1; letter-spacing: 1px; }
  .brand-sub { font-size: 13px; letter-spacing: 5.5px; margin-top: 4px; }

  .card-back .brand { position: absolute; left: 50%; top: 50%; transform: translate(-50%, -50%); color: #e6e6e6; }
  .card-front .brand { position: absolute; left: 50px; top: 30px; color: var(--ink); }

  .holder { position: absolute; left: 50px; top: 112px; color: var(--ink); }
  .holder-name { font-family: "Montserrat", Arial, sans-serif; font-weight: 700; font-size: 17px; }
  .holder-role { font-size: 11px; color: var(--ink-soft); margin-top: 2px; }
  .holder-rule { width: 200px; height: 1px; background: #888; margin: 9px 0 7px; }
  .credentials { font-size: 12px; color: var(--ink); letter-spacing: 0.3px; }
  .credentials .dot { color: var(--accent); margin: 0 5px; }

  .social { position: absolute; right: 36px; top: 128px; display: flex; gap: 5px; }
  .social span { width: 17px; height: 17px; background: var(--ink); border-radius: 2px; }

  .swoosh { position: absolute; left: 0; bottom: 0; }

  .contacts {
    position: absolute;
    right: 30px;
    bottom: 16px;
    list-style: none;
    color: var(--white);
    font-size: 13px;
    text-align: right;
    line-height: 18px;
  }
  .contacts li { display: flex; justify-content: flex-end; align-items: center; gap: 8px; }
  .contacts svg { width: 11px; height: 11px; fill: none; stroke: var(--white); stroke-width: 1.6; }
</style>
</head>
<body>

  <section class="card card-back" aria-label="Card back">
    <div class="brand">
      <span class="brand-mark"></span>
      <div>
        <div class="brand-name">DULOM</div>
        <div class="brand-sub">HOME REMODELING</div>
      </div>
    </div>
  </section>

  <section class="card card-front" aria-label="Card front">
    <div class="brand">
      <span class="brand-mark"></span>
      <div>
        <div class="brand-name">DULOM</div>
        <div class="brand-sub">HOME REMODELING</div>
      </div>
    </div>

    <div class="holder">
      <div class="holder-name">Karim Feltous</div>
      <div class="holder-role">CEO / General Contractor</div>
      <div class="holder-rule"></div>
      <div class="credentials">Licensed<span class="dot">•</span>Insured<span class="dot">•</span>Bonded</div>
    </div>

    <div class="social" aria-label="Social media links"><span></span><span></span><span></span></div>

    <svg class="swoosh" width="540" height="180" viewBox="0 0 540 180" aria-hidden="true">
      <path d="M0 40 C 140 120, 260 36, 540 32 L540 38 C 260 42, 140 126, 0 48 Z" fill="var(--accent)"/>
      <path d="M0 56 C 140 136, 260 52, 540 48 L540 54 C 260 58, 140 142, 0 64 Z" fill="var(--accent)"/>
      <path d="M0 72 C 140 152, 260 70, 540 66 L540 180 L0 180 Z" fill="var(--card-dark)"/>
    </svg>

    <ul class="contacts">
      <li>317-555-0193
        <svg viewBox="0 0 12 12"><path d="M3 1 L5 3.5 L4 5 C5 7 6 8 7.5 8.5 L9 7.5 L11 9.5 L9.5 11 C5 10.5 1.5 7 1 2.5 Z"/></svg></li>
      <li>1-888-DULOM-47
        <svg viewBox="0 0 12 12"><rect x="1.5" y="4" width="9" height="6.5" rx="1"/><path d="M1 4 C3 1.5 9 1.5 11 4"/></svg></li>
      <li>info@dulomhome.com
        <svg viewBox="0 0 12 12"><rect x="1" y="2.5" width="10" height="7"/><path d="M1 2.5 L6 7 L11 2.5"/></svg></li>
      <li>www.dulomhome.com
        <svg viewBox="0 0 12 12"><circle cx="6" cy="6" r="5"/><path d="M1 6 H11 M6 1 C3.5 4 3.5 8 6 11 M6 1 C8.5 4 8.5 8 6 11"/></svg></li>
    </ul>
  </section>

</body>
</html>
```